Allied Health team of Physiotherapists & Occupational Therapists seek a business card design

We have our new logo, we now need our new business cards and stationary. Tidewell: Oedema & Family Clinic is seeking a generic card design to represent our whole team and individual cards for each therapist that incorporates our new logo to communicate our holistic approach that is calming, nuturing, supportive and welcoming.
Our Physiotherapists and Occupational Therapists assess, treat and provide education for people who are at risk of or who have lymphoedema. This is often as a result of treatment for cancer. We provide pre-operative and post-operative management and cancer rehabilitation in our Pilates studio. Our team also consists of Physiotherapists who have a strong interest in pelvic floor and continence management for both men and women.

Target Market(s)

Mainly women health conscious

Industry/Entity Type

Allied Health: Physiotherapy / Occupational Therapy

Contact Information for Business Card

Address: 14 Gallivant Ave Larkfield 3912 Phone: 84316570 fax: 8431 6578 Email: info@tidewellcareservices.com.au Website: tidewellcareservices.com.au Facebook address: facebook.com/TidewellOedemaAndFamilyCareClinic. Room to write appointments. Individual cards need to have name, office email and individual email and professional details

Requirements
Must have
• Logo as per uploaded documents

```html
<!DOCTYPE html>
<html lang="en">
<head>
<meta charset="utf-8">
<title>Tidewell: Oedema &amp; Family Clinic – Business Cards</title>
<link rel="stylesheet" href="https://fonts.googleapis.com/css2?family=Marcellus&family=Source+Sans+3:wght@400;700&family=Roboto:ital,wght@0,400;1,400&display=swap">
<style>
  :root{
    --backdrop:#2e2e2e;
    --card:#f1f1f0;
    --clay:#d98a5e;
    --clay-light:#e8a57c;
    --ink:#2b2b2b;
    --band-text:#fbefe6;
  }
  *{box-sizing:border-box;margin:0;padding:0}
  html,body{width:1200px;height:1138px;overflow:hidden;background:var(--backdrop)}
  .card{position:absolute;width:622px;height:374px;border-radius:16px;background:var(--card);overflow:hidden}
  .card--appointment{left:274px;top:186px}
  .card--contact{left:276px;top:608px}

  .brand{position:absolute;display:flex;align-items:center;justify-content:center;border-radius:50%;
    border:2px solid var(--clay);font-family:"Marcellus",serif;color:var(--clay)}
  .card--appointment .brand{left:478px;top:30px;width:112px;height:112px;font-size:22px}
  .card--contact .brand{left:36px;top:40px;width:216px;height:216px;font-size:42px}

  .title{position:absolute;left:26px;top:58px;font-family:"Marcellus",serif;font-size:29px;color:var(--clay);font-weight:400}

  .form{position:absolute;left:25px;top:0;width:574px;font-family:"Source Sans 3",sans-serif;font-size:18px;color:var(--ink)}
  .row{position:absolute;left:0;display:flex;align-items:flex-end;width:574px;height:22px}
  .row span{white-space:nowrap;line-height:1}
  .line{border-bottom:1.3px solid var(--ink);height:1px;margin-bottom:2px}
  .row--name{top:150px}
  .row--1{top:179px}.row--2{top:208px}.row--3{top:237px}.row--4{top:266px}
  .row .slot{width:272px;margin:0 7px 0 5px}
  .row .date{width:92px;margin:0 7px 0 6px}
  .row .time{flex:1;margin-left:6px}
  .row--name .line{flex:1;margin-left:6px}

  .notice{position:absolute;left:0;bottom:0;width:100%;height:66px;
    background:linear-gradient(90deg,var(--clay) 0%,var(--clay-light) 100%);
    padding:13px 36px 0 37px;font-family:"Source Sans 3",sans-serif;font-size:14px;line-height:21px;color:var(--band-text)}
  .notice strong{font-weight:700}

  .footer-band{position:absolute;left:0;top:0;width:622px;height:374px}

  .person{position:absolute;right:30px;top:40px;text-align:right;font-family:"Roboto",sans-serif;color:var(--ink)}
  .person__name{font-family:"Marcellus",serif;font-size:23px;color:var(--clay);font-weight:400;margin-bottom:4px}
  .person__role{font-style:italic;font-size:15px;line-height:21px}
  .person__field{font-size:15px;line-height:21px}

  .contacts{position:absolute;right:24px;top:229px;list-style:none;font-family:"Roboto",sans-serif;font-size:15.5px;color:var(--ink);text-align:right}
  .contacts li{display:flex;justify-content:flex-end;align-items:center;height:25.8px;gap:5px}
  .contacts svg{width:14px;height:14px;flex:none}
</style>
</head>
<body>

<section class="card card--appointment">
  <div class="brand">Tidewell</div>
  <h1 class="title">Book your Appointment</h1>
  <div class="form">
    <div class="row row--name"><span>Name</span><i class="line"></i></div>
    <div class="row row--1"><span>(1)</span><i class="line slot"></i><span>Date</span><i class="line date"></i><span>Time</span><i class="line time"></i></div>
    <div class="row row--2"><span>(2)</span><i class="line slot"></i><span>Date</span><i class="line date"></i><span>Time</span><i class="line time"></i></div>
    <div class="row row--3"><span>(3)</span><i class="line slot"></i><span>Date</span><i class="line date"></i><span>Time</span><i class="line time"></i></div>
    <div class="row row--4"><span>(4)</span><i class="line slot"></i><span>Date</span><i class="line date"></i><span>Time</span><i class="line time"></i></div>
  </div>
  <p class="notice"><strong>This time is reserved just for you.</strong> If you are unable to keep your appointment, please let us know at least <strong>48 HOURS</strong> in advance so that we may schedule a new time for you.</p>
</section>

<section class="card card--contact">
  <svg class="footer-band" viewBox="0 0 622 374" role="img" aria-label="Decorative clay and sage wave band">
    <defs>
      <linearGradient id="bandFade" x1="0" y1="0" x2="1" y2="0">
        <stop offset="0" stop-color="#e9ad88"/><stop offset="1" stop-color="#d98a5e"/>
      </linearGradient>
    </defs>
    <path d="M0 300 C180 340 420 200 622 200 L622 374 L0 374 Z" fill="url(#bandFade)"/>
  </svg>
  <div class="brand">Tidewell</div>
  <div class="person">
    <h2 class="person__name">Maren Holt</h2>
    <p class="person__role">Physiotherapist</p>
    <p class="person__field">Lymphoedema &amp; Oncology Rehabilitation</p>
    <p class="person__field">Continence &amp; Pelvic Floor</p>
  </div>
  <ul class="contacts">
    <li>8431 6570 <svg viewBox="0 0 16 16"><path d="M2 6c0-2 2-3 6-3s6 1 6 3l-3 1-1-2H6L5 7 2 6zM4 8h8l2 5H2z" fill="#fff"/></svg></li>
    <li>8431 6578 <svg viewBox="0 0 16 16"><path d="M2 6c0-2 2-3 6-3s6 1 6 3l-3 1-1-2H6L5 7 2 6zM4 8h8l2 5H2z" fill="#fff"/></svg></li>
    <li>tidewellcareservices.com.au <svg viewBox="0 0 16 16"><circle cx="8" cy="8" r="6.5" fill="none" stroke="#fff" stroke-width="1.4"/><path d="M1.5 8h13M8 1.5c-3 3.5-3 9.5 0 13M8 1.5c3 3.5 3 9.5 0 13" fill="none" stroke="#fff" stroke-width="1.2"/></svg></li>
    <li>info@tidewellcareservices.com.au <svg viewBox="0 0 16 16"><rect x="1" y="3" width="14" height="10" fill="#fff"/><path d="M1 3l7 6 7-6" fill="none" stroke="#d98a5e" stroke-width="1.2"/></svg></li>
    <li>14 Gallivant Ave, Larkfield 3912 <svg viewBox="0 0 16 16"><path d="M8 1a5 5 0 0 1 5 5c0 4-5 9-5 9S3 10 3 6a5 5 0 0 1 5-5z" fill="#fff"/><circle cx="8" cy="6" r="1.8" fill="#d98a5e"/></svg></li>
  </ul>
</section>

</body>
</html>
```